Luxury Real Estate Website, Midwest, United States

We need web design services for a luxury website. We need IDX Integration with our MLS. We want this to be a very simple website with amazing graphics. We want it to link up with our MailChimp account in order to generate leads through a "More Information" Pop up on the main page. We want the main page to be covered with one large graphic that is a rolling slideshow of active listings of $400,000 and up from the IDX Integration. We need this website to give a very exclusive and sleek look. Lots of black is good... I will upload our logos in Black and Silver. We will also need an "About" page that we are going to call "Qeno Info". We want our graphics to be extremely impressive. Keep in mind, we are a company in the Midwest of the United States, and our real estate has a different look than homes in California or Florida. We need graphics that are realistic for the Midwest, yet still high-end.
Target Market(s)
Luxury Homeowners in the Midwest United States. The graphics needs to be pristine.
Industry/Entity Type
Real Estate
Coding
Coded - Design and coding required
Number of Pages Required
3 page
Requirements
Must have
- Large graphics with IDX Integration. The photos of real estate need to represent real estate that is common in the Midwest, United States. We also need MailChimp integration. We need a pop up that is titled "My Free Market Analysis" that makes them fill out a contact form asking for Full Name, Email Address, Phone Number and Address. This needs to be a pop up on the front page and will integrate with our MailChimp account. We also need a page called "About Qe No Home". And another page where clients can download informational PDFs. The main component needs to be a front page search engine connected with the IDX to access active listings from our MLS. I attached our logos and a sample front page of a website. I would love for ours to look similar.
Nice to have
- Lake House photos on midwest lakes are a plus.
Should not have
- Should not have clutter. This website needs to be clean, luxurious and exclusive.

```html
<!DOCTYPE html>
<html lang="en">
<head>
<meta charset="utf-8">
<title>Hearthline Realty Group</title>
<link href="https://fonts.googleapis.com/css2?family=Poppins:ital,wght@0,300;0,400;0,500;0,600;1,400&display=swap" rel="stylesheet">
<style>
:root{
  --ink:#111111;
  --text:#2b2b2b;
  --muted:#6b6b6b;
  --line:#e3e3e3;
  --band:#f3f3f3;
  --white:#ffffff;
  --panel:rgba(20,20,20,.88);
  --frame:#4a5560;
}
*{box-sizing:border-box;margin:0;padding:0}
html,body{width:1200px;height:4091px;overflow:hidden}
body{position:relative;background:var(--white);font-family:'Poppins',sans-serif;color:var(--text)}
.abs{position:absolute}
a{color:inherit;text-decoration:none}

/* header */
.site-header{left:0;top:0;width:1200px;height:106px;background:var(--white)}
.brand{left:160px;top:30px;display:flex;align-items:center;gap:10px}
.brand-mark{width:12px;height:12px;background:var(--ink)}
.brand-name{font-size:19px;font-weight:500;color:var(--ink);line-height:1.05;letter-spacing:.5px;width:170px}
.main-nav{left:400px;top:40px;display:flex;gap:0}
.main-nav a{font-size:15px;color:var(--ink);margin-right:56px}

/* hero */
.hero{left:0;top:106px;width:1200px;height:612px;background:linear-gradient(180deg,#4f8fd6 0%,#8fbbe6 35%,#c9c9c4 55%,#6d7a5a 80%,#3f6a2c 100%)}
.hero-cut{left:0;top:600px;width:1200px;height:120px}
.search-panel{left:160px;top:688px;width:880px;height:158px;background:var(--white);box-shadow:0 4px 16px rgba(0,0,0,.12)}
.search-title{top:34px;left:0;width:100%;text-align:center;font-size:19px;font-weight:400;letter-spacing:.6px;color:var(--ink)}
.search-fields{left:24px;top:88px;display:flex;gap:24px;align-items:flex-end}
.field{width:115px;border-bottom:1px solid #9a9a9a;font-size:11px;padding-bottom:5px;color:var(--ink);display:flex;justify-content:space-between}
.field.wide{width:152px}
.btn-search{background:var(--ink);color:var(--white);font-size:12px;font-weight:500;padding:9px 20px;letter-spacing:.5px}

/* welcome */
.welcome-back{left:183px;top:958px;width:228px;height:272px;background:linear-gradient(160deg,#2a2d33,#111)}
.welcome-photo{left:297px;top:1012px;width:253px;height:293px;background:linear-gradient(180deg,#3f7ac9 0%,#8bb3de 45%,#6f86a3 70%,#2f5f86 100%);box-shadow:0 6px 18px rgba(0,0,0,.3)}
.welcome-text{left:610px;top:972px;width:430px}
.section-heading{font-size:26px;font-weight:400;color:var(--ink);line-height:1.25;letter-spacing:.3px}
.lead{margin-top:30px;font-size:11px;line-height:1.9;color:var(--text)}
.dropcap{float:left;font-size:64px;line-height:.85;margin:4px 10px 0 0;color:var(--ink);font-weight:300}
.btn-dark{display:inline-block;margin-top:26px;background:var(--ink);color:var(--white);font-size:10px;padding:9px 15px;letter-spacing:.4px}
.divider{left:160px;width:880px;height:2px;background:var(--line)}

/* latest */
.center-title{left:0;width:1200px;text-align:center;font-size:26px;font-weight:400;color:var(--ink);letter-spacing:.4px}
.listing{background:linear-gradient(180deg,#8fb2d3 0%,#c6c2b6 40%,#8a5a45 65%,#4e7c34 100%)}
.listing-left{left:248px;top:1545px;width:175px;height:265px}
.listing-right{left:778px;top:1545px;width:178px;height:265px;background:linear-gradient(180deg,#7ea7d0 0%,#d8c7a8 45%,#b38b5a 65%,#5d8a3a 100%)}
.listing-main{left:410px;top:1500px;width:382px;height:356px;border:9px solid var(--frame);background:linear-gradient(180deg,rgba(70,80,90,.85),rgba(45,60,55,.9))}
.listing-caption{left:0;top:138px;width:100%;text-align:center;color:var(--white);font-size:17px;line-height:1.45}
.arrow{width:40px;height:24px}

/* midwest */
.map-area{left:160px;top:1925px;width:410px;height:300px;background:linear-gradient(180deg,#fafafa,#eeeeee);border:1px solid #dcdcdc}
.region-text{left:670px;top:2005px;width:370px}
.region-sub{margin-top:26px;font-size:15px;font-weight:500;color:var(--ink)}
.body-sm{margin-top:18px;font-size:11px;line-height:1.9}

/* new properties */
.band{left:0;top:2368px;width:1200px;height:462px;background:var(--band)}
.new-text{left:160px;top:2448px;width:300px}
.specs{margin-top:22px;display:flex;gap:18px;font-size:9px;color:var(--ink);align-items:center}
.spec{display:flex;align-items:center;gap:5px}
.spec i{display:inline-block;width:14px;height:10px;border:1.5px solid var(--ink)}
.prop-title{margin-top:14px;font-size:19px;font-weight:500;line-height:1.3;color:var(--ink)}
.price{margin-top:22px;font-size:20px;font-weight:600;color:var(--ink)}
.new-photo{left:505px;top:2474px;width:615px;height:418px;background:linear-gradient(180deg,#5e93cf 0%,#9fbf8a 25%,#a88a73 50%,#8a6a55 75%,#4b6a30 100%)}

/* testimonials */
.quote{left:310px;top:3090px;width:580px;text-align:center;font-size:12.5px;font-style:italic;line-height:1.75;color:var(--text)}
.quote-name{left:0;top:3172px;width:1200px;text-align:center;font-size:13px;font-weight:500;color:var(--ink)}

/* contact */
.city-band{left:0;top:3350px;width:1200px;height:418px;background:linear-gradient(180deg,#7ab0e0 0%,#a9c9e6 30%,#a87a52 55%,#6b5a3a 70%,#3a4a44 100%)}
.contact-card{left:448px;top:3410px;width:306px;height:292px;background:var(--panel);color:var(--white);padding:48px 0 0 58px}
.contact-row{display:flex;gap:22px;align-items:flex-start;font-size:12px;line-height:1.55;margin-bottom:36px}
.contact-row svg{flex:none;margin-top:2px}

/* footer */
.footer-brand{left:160px;top:3838px}
.footer-col{top:3826px}
.footer-col h4{font-size:16px;font-weight:500;color:var(--ink);margin-bottom:12px}
.footer-col li{list-style:none;font-size:11.5px;line-height:2.05;color:var(--text)}
.social{display:flex;gap:12px;align-items:center;margin-bottom:22px}
.social span{width:20px;height:20px;border-radius:50%;background:var(--ink)}
.legal{left:0;top:4036px;width:1200px;text-align:center;font-size:11px;color:var(--text)}
.legal-line{left:160px;top:4012px;width:880px;height:1px;background:var(--line)}
</style>
</head>
<body>

<header class="site-header abs">
  <div class="brand abs"><span class="brand-mark"></span><span class="brand-name">HEARTHLINE<br><small style="font-size:9px;letter-spacing:2px">REALTY GROUP</small></span></div>
  <nav class="main-nav abs">
    <a href="#">Home</a><a href="#">Qeno Info</a><a href="#">About Qe No Home</a><a href="#">Downloads</a><a href="#">Contact us</a>
  </nav>
</header>

<section class="hero abs" role="img" aria-label="Large two-storey Midwest family home with white siding and grey roof on a green lawn under blue sky"></section>
<svg class="hero-cut abs" viewBox="0 0 1200 120" preserveAspectRatio="none"><path d="M0 118 L0 118 Q600 70 1200 30 L1200 120 L0 120 Z" fill="#ffffff"/></svg>

<div class="search-panel abs">
  <div class="search-title abs">FIND YOUR DREAM HOME TODAY</div>
  <div class="search-fields abs">
    <div class="field">City</div>
    <div class="field wide">Property Type <span>▾</span></div>
    <div class="field wide">Sale Type <span>▾</span></div>
    <div class="field">Min. Price</div>
    <div class="field">Max. Price</div>
    <div class="btn-search">SEARCH</div>
  </div>
</div>

<div class="welcome-back abs"></div>
<div class="welcome-photo abs" role="img" aria-label="City skyline of glass towers beside a river at dusk"></div>
<div class="welcome-text abs">
  <h2 class="section-heading">WELCOME TO<br>HEARTHLINE REALTY GROUP</h2>
  <p class="lead"><span class="dropcap">R</span>ealty Group explicabo unde omnis iste natus error sit voluptatem accusantium doloremque laudantium, totam rem aperiam, eaque ipsa quae ab illo inventore veritatis et quasi architecto beatae vitae dicta sunt explicabo. Nemo enim ipsam voluptatem quia voluptas sit aspernatur aut odit aut fugit, sed quia consequuntur magni dolores eos qui ratione voluptatem sequi nesciunt neque porro quisquam est, qui dolorem ipsum quia dolor sit amet consectetur adipisci velit sed quia non numquam eius modi tempora incidunt ut labore et dolore magnam aliquam quaerat.</p>
  <a class="btn-dark" href="#">READ MORE</a>
</div>

<div class="divider abs" style="top:1380px"></div>

<h2 class="center-title abs" style="top:1424px">LATEST PROPERTIES</h2>
<svg class="arrow abs" style="left:160px;top:1648px" viewBox="0 0 40 24"><path d="M38 12H3M12 3L3 12l9 9" fill="none" stroke="#bbbbbb" stroke-width="2"/></svg>
<div class="listing listing-left abs" role="img" aria-label="Brick and siding suburban house with red door"></div>
<div class="listing-right abs" role="img" aria-label="Brick townhouses along a lawn"></div>
<div class="listing-main abs" role="img" aria-label="Row of suburban homes beside a pond">
  <p class="listing-caption abs">Nemo enim ipsam volupt<br>quia voluptas sit asperneino<br>enim ipsam voluptam</p>
</div>
<svg class="arrow abs" style="left:1000px;top:1648px" viewBox="0 0 40 24"><path d="M2 12h35M28 3l9 9-9 9" fill="none" stroke="#bbbbbb" stroke-width="2"/></svg>

<div class="divider abs" style="top:1930px"></div>

<div class="map-area abs" role="img" aria-label="Outline map of the United States divided into states"></div>
<div class="region-text abs">
  <h2 class="section-heading">Sed ut perspiciatis unde<br>omnis irm dotaeaua</h2>
  <p class="region-sub">Midwest, United states</p>
  <p class="body-sm">Sb illo inventore ver itatis et quasi architecto beatae vitae dicta sunt explicabo. Nemo enim ipsam voluptatem quia voluptas sit aspe rnatur aut odit aut fugit, sed quia conse quu ntur magni doloreeos qui ratione voluptatem sequi nesciuntue porro quisum est, qui dolore enim ipsam voluptatem quia voluptas sit aspernatur aut odit aut fugit, sed quia conse quu ntur magni dolore.</p>
</div>

<div class="band abs"></div>
<div class="new-text abs">
  <h2 class="section-heading">NEW PROPERTIES</h2>
  <div class="specs"><span class="spec"><i></i>1200 ft²</span><span class="spec"><i></i>3</span><span class="spec"><i></i>2</span></div>
  <h3 class="prop-title">Sb illo inventore ver architeceatae vitae dica sun</h3>
  <p class="body-sm" style="margin-top:12px">Sb illo inventore ver itatis et quasi architecto beatae vitae dicta sunt explicabo. Nemo enim ipsam voluptatem quia voluptas sit aspe rnatur aut odit aut fugit, sed quia conse quu ntur magni doloreeo.</p>
  <p class="price">$1,200.00</p>
</div>
<div class="new-photo abs" role="img" aria-label="Large brick house with steep gabled roofs, trees and shrubs"></div>

<h2 class="center-title abs" style="top:3022px">WHAT OUR CLIENTS SAY</h2>
<svg class="arrow abs" style="left:218px;top:3110px" viewBox="0 0 40 24"><path d="M38 12H3M12 3L3 12l9 9" fill="none" stroke="#bbbbbb" stroke-width="2"/></svg>
<p class="quote abs">Lorem ipsum dolor sit amet, consectetur adipiscing elit, sed do eiusmod tempor incididunt ut labore dolore magna aliqua. Ut enim ad minim veniam,Lorem ipsum dolor sit amet, consectetur adipiscing elised do eiusmod tempor incididunt ut labore et dolore magna aliqua. Ut enim ad minim veniam,</p>
<svg class="arrow abs" style="left:940px;top:3110px" viewBox="0 0 40 24"><path d="M2 12h35M28 3l9 9-9 9" fill="none" stroke="#bbbbbb" stroke-width="2"/></svg>
<p class="quote-name abs">Dana Whitfield, City Name</p>

<div class="city-band abs" role="img" aria-label="Midwest city skyline across a river lined with autumn trees"></div>
<div class="contact-card abs">
  <div class="contact-row"><svg width="18" height="22" viewBox="0 0 18 22"><path d="M9 21s7-7.5 7-12.5a7 7 0 0 0-14 0C2 13.5 9 21 9 21z" fill="none" stroke="#fff" stroke-width="1.5"/><circle cx="9" cy="8.5" r="2.5" fill="none" stroke="#fff" stroke-width="1.5"/></svg><span>412 Linden Crest Avenue,<br>Midwest, United states</span></div>
  <div class="contact-row"><svg width="20" height="20" viewBox="0 0 20 20"><path d="M4 1.5l3.5 3.5-2 2.5c1.5 3 3.5 5 6.5 6.5l2.5-2 3.5 3.5-2.5 3C8.5 17.5 2.5 11.5 1 4z" fill="none" stroke="#fff" stroke-width="1.5" stroke-linejoin="round"/></svg><span>Phone: 800 555 0142<br>Phone: 800 555 0178</span></div>
  <div class="contact-row"><svg width="20" height="16" viewBox="0 0 20 16"><rect x="1" y="1" width="18" height="14" fill="none" stroke="#fff" stroke-width="1.5"/><path d="M1 1l9 7 9-7" fill="none" stroke="#fff" stroke-width="1.5"/></svg><span>info@example.com<br>founder@example.com</span></div>
</div>

<div class="brand footer-brand abs"><span class="brand-mark"></span><span class="brand-name">HEARTHLINE<br><small style="font-size:9px;letter-spacing:2px">REALTY GROUP</small></span></div>
<div class="footer-col abs" style="left:380px"><h4>Links</h4><ul><li>Home</li><li>Qeno Info</li><li>About Qe No Home</li><li>Downloads</li><li>Contact us</li></ul></div>
<div class="footer-col abs" style="left:537px"><h4>Real Estate</h4><ul><li>Sed uerspiciatism</li><li>Comnisteatusil</li><li>Sed uerspiciatism</li><li>Comnisteatusil</li><li>Perspiciatis unde</li></ul></div>
<div class="footer-col abs" style="left:723px"><h4>Connect</h4>
  <div class="social"><svg width="22" height="16" viewBox="0 0 22 16"><rect x="0" y="0" width="22" height="16" fill="#111"/><path d="M1 1l10 8 10-8" fill="none" stroke="#fff" stroke-width="1.5"/></svg><span></span><span></span><span></span></div>
  <h4>Policies</h4><ul><li>Privacy</li><li>Complaint and Feedback</li></ul></div>
<div class="footer-col abs" style="left:926px"><h4>Other Links</h4><ul><li>Sed uerspiciatis</li><li>Sed uerspiciatism</li><li>Comnisteatusil</li><li>Perspiciatis unde</li><li>Sed uerspiciatism</li></ul></div>
<div class="legal-line abs"></div>
<p class="legal abs">© 2018 Hearthline Realty Group. All Rights are Reserved Privacy Policy | Terms of Use | Contact</p>

</body>
</html>
```